R. Talmont Realty, Inc business card (2 sided), letterhead (1 sided) & #10 envelope (1 sided)

business card of standard size utilizing the attached logo. Side one with logo, Owen Talmont (my name), President / Broker (title), 805-317-2684 (phone), www.rtalmontrealty.example (website), 1726 Harlow Avenue, Suite 4052 San Luis Obiso, CA 93628 (business address) owen.rtalmontrealty@mailbox.example (e-mail address),
Side two - Log

Letterhead and #10 envelope in the same theme
Updates

Project Deadline Extended
Reason: I think a 2 day deadline may be a bit ambitious on my part. I have extended the deadline to 4 days. Thanks!

Industry/Entity Type

Business

```html
<!DOCTYPE html>
<html lang="en">
<head>
<meta charset="utf-8">
<title>R. Talmont Realty, Inc — Stationery</title>
<link href="https://fonts.googleapis.com/css2?family=Open+Sans:wght@400;600;700&display=swap" rel="stylesheet">
<style>
:root{
  --teal-dark:#164f6c;
  --teal:#1f6b8f;
  --teal-light:#3a94bd;
  --ink:#333;
  --muted:#555;
  --paper:#fff;
  --faint:#dfe4ea;
  --stage:#ecebe8;
}
*{box-sizing:border-box;margin:0;padding:0}
html,body{width:1200px;height:698px;overflow:hidden}
body{background:var(--stage);font-family:"Open Sans",Arial,sans-serif;color:var(--ink);position:relative}
.sheet{position:absolute;background:var(--paper);box-shadow:0 1px 3px rgba(0,0,0,.25);overflow:hidden}
.band{position:absolute;left:0;right:0;background:linear-gradient(90deg,var(--teal-dark),var(--teal),var(--teal-light),var(--teal),var(--teal-dark));color:#fff;text-align:center;white-space:nowrap}
.band::before{content:"";position:absolute;left:0;right:0;top:-3px;height:1px;background:var(--teal)}
.brand{display:flex;align-items:center;gap:4px;color:var(--teal);font-weight:600;white-space:nowrap;line-height:1}
.brand .mark{background:var(--teal);flex:none}
.brand.light{color:#fff}
.brand.light .mark{background:#fff}
.contact{font-size:5px;line-height:8.5px;color:var(--muted);white-space:nowrap}
.contact li{list-style:none;display:flex;align-items:center;gap:2px}
.dot{width:4px;height:4px;border-radius:50%;background:var(--teal);display:inline-block;flex:none}
.watermark{position:absolute;color:var(--faint);font-weight:600;white-space:nowrap}
.caption{position:absolute;font-size:14px;color:#444;transform:translateX(-50%)}
.address{font-size:6px;line-height:9px;color:var(--muted);white-space:nowrap}
.name{color:var(--teal);font-weight:700;font-size:8px;white-space:nowrap}
.title{font-size:5.5px;font-weight:600;color:var(--muted);white-space:nowrap}
.badge{position:absolute;width:13px;height:13px;background:#222}
</style>
</head>
<body>

<!-- Letterhead option 1 -->
<section class="sheet letterhead-1" style="left:16px;top:44px;width:341px;height:440px">
  <div class="brand" style="position:absolute;left:14px;top:20px;font-size:10px"><span class="mark" style="width:7px;height:7px"></span>R. Talmont Realty, Inc</div>
  <ul class="contact" style="position:absolute;right:6px;top:8px;border-left:1px solid #bbb;padding-left:3px;font-size:4.6px">
    <li><span class="dot"></span>805-317-2684</li>
    <li><span class="dot"></span>owen.rtalmontrealty@mailbox.example</li>
    <li><span class="dot"></span>www.rtalmontrealty.example</li>
    <li>BRE License # 02475318</li>
  </ul>
  <div class="watermark" style="left:56px;top:230px;font-size:20px">R. Talmont Realty, Inc</div>
  <div class="band" style="bottom:0;height:24px;font-size:6px;line-height:24px">1726 Harlow Avenue, Suite 4052, San Luis Obispo, CA 93628</div>
</section>
<div class="caption" style="left:177px;top:494px">Option-1</div>

<!-- Letterhead option 2 -->
<section class="sheet letterhead-2" style="left:382px;top:44px;width:341px;height:438px">
  <div class="brand" style="position:absolute;left:0;right:0;top:30px;justify-content:center;font-size:11px"><span class="mark" style="width:7px;height:7px"></span>R. Talmont Realty, Inc</div>
  <div class="watermark" style="left:40px;top:350px;font-size:22px">R. Talmont Realty, Inc</div>
  <div class="contact" style="position:absolute;left:0;right:0;top:406px;text-align:center;font-size:5.5px">
    <span class="dot"></span> 805-317-2684 &nbsp; <span class="dot"></span> owen.rtalmontrealty@mailbox.example &nbsp; <span class="dot"></span> www.rtalmontrealty.example<br>
    1726 Harlow Avenue, Suite 4052, San Luis Obispo, CA 93628 &nbsp;|&nbsp; BRE License # 02475318
  </div>
</section>
<div class="caption" style="left:548px;top:494px">Option-2</div>

<!-- Envelope backs -->
<section class="sheet envelope-back-teal" style="left:798px;top:0;width:402px;height:80px;background:linear-gradient(90deg,var(--teal-dark),var(--teal-light) 50%,var(--teal-dark));box-shadow:none">
  <svg width="402" height="80" style="position:absolute;inset:0" aria-hidden="true"><polyline points="0,50 30,80 372,80 402,50" fill="none" stroke="#e6eef3" stroke-width="1"/></svg>
  <div class="brand light" style="position:absolute;left:0;right:0;top:34px;justify-content:center;font-size:11px"><span class="mark" style="width:7px;height:7px"></span>R. Talmont Realty, Inc</div>
</section>
<section class="sheet envelope-back" style="left:772px;top:100px;width:384px;height:165px">
  <svg width="384" height="165" style="position:absolute;inset:0" aria-hidden="true"><polyline points="0,0 30,42 354,42 384,0" fill="none" stroke="#777" stroke-width="1"/></svg>
  <div class="brand" style="position:absolute;left:0;right:0;top:22px;justify-content:center;font-size:9px"><span class="mark" style="width:6px;height:6px"></span>R. Talmont Realty, Inc</div>
</section>

<!-- Envelope fronts -->
<section class="sheet envelope-front-1" style="left:744px;top:173px;width:382px;height:165px">
  <div class="brand" style="position:absolute;left:14px;top:36px;font-size:12px"><span class="mark" style="width:8px;height:8px"></span>R. Talmont Realty, Inc</div>
  <p class="address" style="position:absolute;left:18px;top:68px">1726 Harlow Avenue, Suite 4052<br>San Luis Obispo, CA 93628</p>
  <div class="band" style="bottom:0;height:20px;font-size:7px;line-height:20px;text-align:left;padding-left:18px;letter-spacing:1px;background:radial-gradient(ellipse at 66% 50%,var(--teal-light),var(--teal-dark) 60%)">www.rtalmontrealty.example</div>
</section>
<div class="caption" style="left:922px;top:342px">Front-1</div>

<section class="sheet envelope-front-2" style="left:744px;top:366px;width:382px;height:165px">
  <div class="brand" style="position:absolute;left:14px;top:36px;font-size:12px"><span class="mark" style="width:8px;height:8px"></span>R. Talmont Realty, Inc</div>
  <p class="address" style="position:absolute;left:18px;top:68px">1726 Harlow Avenue, Suite 4052<br>San Luis Obispo, CA 93628</p>
  <div class="band" style="bottom:0;height:20px;font-size:7px;line-height:20px;letter-spacing:1px">www.rtalmontrealty.example</div>
</section>
<div class="caption" style="left:922px;top:537px">Front-2</div>

<!-- Business card front 1 -->
<section class="sheet card-front-1" style="left:22px;top:550px;width:193px;height:111px">
  <div class="brand" style="position:absolute;left:8px;top:42px;font-size:7px;flex-direction:column;align-items:flex-start;gap:2px"><span style="display:flex;gap:3px;align-items:center"><span class="mark" style="width:5px;height:5px"></span>R. Talmont</span><span>Realty, Inc</span></div>
  <div style="position:absolute;left:102px;top:12px;border-left:1px solid #bbb;padding-left:4px">
    <div class="name">Owen Talmont</div>
    <div class="title">President / Broker</div>
    <ul class="contact" style="margin-top:6px;font-size:4.2px;line-height:8px">
      <li><span class="dot"></span>805-317-2684</li>
      <li><span class="dot"></span>owen.rtalmontrealty@mailbox.example</li>
      <li><span class="dot"></span>www.rtalmontrealty.example</li>
      <li>BRE License # 02475318</li>
    </ul>
  </div>
  <div class="badge" style="left:164px;top:82px" role="img" aria-label="Membership badge"></div>
  <div class="band" style="bottom:0;height:13px;font-size:4.5px;line-height:13px;text-align:left;padding-left:10px">1726 Harlow Avenue, Suite 4052, San Luis Obispo, CA 93628</div>
</section>
<div class="caption" style="left:118px;top:667px">Front-1</div>

<!-- Business card front 2 -->
<section class="sheet card-front-2" style="left:233px;top:550px;width:193px;height:111px">
  <div class="brand" style="position:absolute;left:0;right:0;top:22px;justify-content:center;font-size:8px"><span class="mark" style="width:5px;height:5px"></span>R. Talmont Realty, Inc</div>
  <div style="position:absolute;right:104px;top:54px;text-align:right">
    <div class="name">Owen Talmont</div>
    <div class="title">President / Broker</div>
    <p class="address" style="font-size:4.3px;line-height:7px;margin-top:2px">1726 Harlow Avenue, Suite 4052<br>San Luis Obispo, CA 93628</p>
  </div>
  <ul class="contact" style="position:absolute;left:94px;top:54px;border-left:1px solid #bbb;padding-left:3px;font-size:4.2px;line-height:9px">
    <li><span class="dot"></span>805-317-2684</li>
    <li><span class="dot"></span>owen.rtalmontrealty@mailbox.example</li>
    <li>BRE License # 02475318</li>
  </ul>
  <div class="badge" style="left:166px;top:82px" role="img" aria-label="Membership badge"></div>
  <div class="band" style="bottom:0;height:14px;font-size:6px;font-weight:600;line-height:14px">www.rtalmontrealty.example</div>
</section>
<div class="caption" style="left:329px;top:667px">Front-2</div>

<!-- Business card front 3 -->
<section class="sheet card-front-3" style="left:439px;top:550px;width:193px;height:111px">
  <div class="brand" style="position:absolute;left:8px;top:14px;font-size:8px"><span class="mark" style="width:5px;height:5px"></span>R. Talmont Realty, Inc</div>
  <div class="badge" style="left:168px;top:8px" role="img" aria-label="Membership badge"></div>
  <ul class="contact" style="position:absolute;left:12px;top:54px;font-size:4.2px;line-height:9px">
    <li><span class="dot"></span>805-317-2684</li>
    <li><span class="dot"></span>owen.rtalmontrealty@mailbox.example</li>
    <li><span class="dot"></span>www.rtalmontrealty.example</li>
    <li>BRE License # 02475318</li>
  </ul>
  <div style="position:absolute;right:8px;top:64px;text-align:center">
    <div class="name">Owen Talmont</div>
    <div class="title">President / Broker</div>
  </div>
  <div class="band" style="bottom:0;height:13px;font-size:4.5px;line-height:13px;text-align:left;padding-left:10px">1726 Harlow Avenue, Suite 4052, San Luis Obispo, CA 93628</div>
</section>
<div class="caption" style="left:535px;top:667px">Front-3</div>

<!-- Business card back -->
<section class="sheet card-back" style="left:649px;top:548px;width:193px;height:111px;background:radial-gradient(ellipse at 50% 40%,var(--teal-light),var(--teal) 45%,var(--teal-dark))">
  <div class="brand light" style="position:absolute;left:0;right:0;top:40px;justify-content:center;font-size:11px"><span class="mark" style="width:7px;height:7px"></span>R. Talmont Realty, Inc</div>
  <div style="position:absolute;left:0;right:0;top:87px;text-align:center;color:#fff;font-size:6px;font-weight:600;letter-spacing:1px;white-space:nowrap">www.rtalmontrealty.example</div>
</section>

</body>
</html>
```